Equipment Finance Specialist I work with companies who need the funds to buy their equipment

I would like a business card that stands out on the shelves. I want to be able to hand it to someone and say WOW. This card should have my logo.
You can put color into it I am very open on design and color

What my company does is we deal with dealerships that sell equipment such as Dump Trucks garbage trucks tractors trailers. Customers get referred to us and depending on their time in business we will ask for the following items

Companies that have been in business for more than two years we have a credit application program up to 250K . With this program we need the following items Credit application filled out(which is what I would like to be able for the customer to click on my website to get.) as well as three current month bank statements.

Deals over 250k we will need the following items

2 years business tax returns
2 years personal tax returns
Profit & Loss statement
Personal Financial Statement

what we do
100% FINANCING
SEASONAL PAYMENTS
LOAN BALLOON PAYMENTS
TRAC LEASING
LOW-INTEREST REFINANCING RATES
DEBT CONSOLIDATION

We specialize in creative financing solutions and offer a variety of reliable, flexible and expandable lending choices.

Target Market(s)

Trucking Companies

Industry/Entity Type

Trucking Company

Contact Information for Business Card

* $250,000 Application only Program
* Loans from $30,000 to 5,000,000
* Competitive Interest Rates

Font styles to use
Serif
Sans Serif

Colors

Designer to choose colors to be used in the design.

Requirements
Must have
• On the back of the card.
• * $250,000 Application only Program
• * Loans from $30,000 to 5,000,000
• My name, email, website. address
• * Competitive Interest Rates
• * 100% Financing
Nice to have
• I want my logo to pop on the card
• My logo is the great one I would like to use
Should not have
• I am up for your creativity as well

```html
<!DOCTYPE html>
<html lang="en">
<head>
<meta charset="utf-8">
<title>Summit Lending – Business Card</title>
<link rel="stylesheet" href="https://fonts.googleapis.com/css2?family=Lato:wght@400;700;900&display=swap">
<style>
  :root{
    --canvas:#e9ebee;
    --ink:#111214;
    --paper:#ffffff;
    --navy:#23336b;
    --red:#e3222b;
    --muted:#2b2b2b;
  }
  *{box-sizing:border-box;margin:0;padding:0}
  html,body{width:1200px;height:858px;overflow:hidden}
  body{background:var(--canvas);font-family:"Lato",Arial,sans-serif;position:relative}

  .card{position:absolute;width:560px;height:320px;border-radius:18px;overflow:hidden;
        box-shadow:0 10px 30px rgba(0,0,0,.18)}
  .card--front{left:30px;top:269px;background:var(--ink)}
  .card--back{left:610px;top:269px;background:var(--paper)}

  /* front */
  .front-brand{position:absolute;inset:0;display:flex;align-items:center;justify-content:center;gap:20px}
  .brand-dot{width:84px;height:84px;border-radius:50%;background:#fff}
  .brand-name{color:#fff;font-weight:900;font-size:42px;line-height:1;letter-spacing:1px;text-transform:uppercase}

  /* back */
  .back-band{position:absolute;inset:0}
  .back-brand{position:absolute;right:36px;top:38px;color:var(--navy);font-weight:900;
              font-size:30px;letter-spacing:.5px;text-transform:uppercase}
  .offer-list{position:absolute;left:70px;top:104px;list-style:none;text-align:right;width:220px}
  .offer-list li{font-size:13.5px;color:var(--muted);line-height:21px;position:relative;padding-right:14px}
  .offer-list li::after{content:"";position:absolute;right:0;top:8px;width:6px;height:6px;border-radius:50%;background:var(--red)}
  .offer-list .accent{color:var(--red)}

  .person{position:absolute;right:36px;top:102px;text-align:right}
  .person-name{color:var(--navy);font-weight:900;font-size:26px;line-height:1;text-transform:uppercase}
  .person-role{color:#fff;font-size:13px;margin-top:6px}

  .contact-list{position:absolute;right:30px;top:170px;list-style:none;text-align:right}
  .contact-list li{color:#fff;font-size:13px;line-height:22px;display:flex;align-items:center;justify-content:flex-end;gap:9px}
  .contact-list svg{width:12px;height:12px;fill:none;stroke:#fff;stroke-width:1.6}

  .address{position:absolute;left:178px;top:240px;color:#fff;font-size:14px;line-height:20px}
  .mark-circle{position:absolute;left:40px;top:206px;width:112px;height:112px;border-radius:50%;
               background:var(--navy);border:5px solid #fff}
</style>
</head>
<body>

<section class="card card--front" aria-label="Card front">
  <div class="front-brand">
    <span class="brand-dot"></span>
    <span class="brand-name">Summit Lending</span>
  </div>
</section>

<section class="card card--back" aria-label="Card back">
  <svg class="back-band" viewBox="0 0 560 320" preserveAspectRatio="none" aria-hidden="true">
    <path d="M110 222 L320 222 L390 150 L560 150 L560 300 L110 300 Z" fill="var(--ink)"/>
  </svg>

  <div class="back-brand">Summit Lending</div>

  <ul class="offer-list">
    <li>$250,000 Application only Program</li>
    <li>Competitive Interest Rates</li>
    <li>Loans from $30,000 to 5,000,000</li>
    <li><span class="accent">100%</span> Financing</li>
  </ul>

  <div class="person">
    <div class="person-name">Mark Ellison</div>
    <div class="person-role">Managing Partner</div>
  </div>

  <ul class="contact-list">
    <li>555 210 4477
      <svg viewBox="0 0 12 12"><path d="M2 1.5 L4 1.5 L5 4 L3.8 5 Q5 7.5 7 8.2 L8 7 L10.5 8 L10.5 10 Q5 10.5 2 4 Z"/></svg></li>
    <li>mark@summitlending.com
      <svg viewBox="0 0 12 12"><rect x="1" y="2.5" width="10" height="7"/><path d="M1 2.5 L6 6.5 L11 2.5"/></svg></li>
    <li>www.summitlending.com
      <svg viewBox="0 0 12 12"><circle cx="6" cy="6" r="5"/><path d="M1 6 H11 M6 1 Q3 6 6 11 Q9 6 6 1"/></svg></li>
  </ul>

  <div class="mark-circle"></div>
  <p class="address">48 Harbour Road, Suite B<br>Leeds, UK LS1 4BT</p>
</section>

</body>
</html>
```